Help design website for "Brightwater Civic Advisors" to advance the common good

Here is the Google doc link that lays out the design:

https://files.plumrivet.example/sheet/d/7QmTzR2wLx9KpVbN4hJcY8sEaUoFdG3iXkMnPq5rWt6/edit?usp=sharing

Here is the Google drive folder with the logos and photos: https://vault.plumrivet.example/open?id=4HkWp9LzQe2TxRvN8mBaYc3DsUoJfG6

The testimonials are being gathered and will be shared by Friday, 1/4.

The winner will also have to migrate the coding files to my hosting site.

Thank you for your help! Looking forward to seeing your designs.

Target Market(s)

Prospective clients

Industry/Entity Type

Non Profit

Coding

Coded - Design and coding required

Number of Pages Required

5+ page

Requirements
Must have
• Noted in the Google doc regarding layout.
Nice to have

```html
<!DOCTYPE html>
<html lang="en">
<head>
<meta charset="utf-8">
<title>Brightwater Civic Advisors</title>
<link href="https://fonts.googleapis.com/css2?family=Poppins:wght@400;500;600;700&family=Open+Sans:wght@400;600;700&display=swap" rel="stylesheet">
<style>
:root{
  --blue:#3b87d3;
  --navy:#2a2c38;
  --mist:#f3f1f1;
  --ink:#1e1e22;
  --body:#4a4a4f;
  --line:#c9c9cf;
  --white:#ffffff;
}
*{box-sizing:border-box;margin:0;padding:0}
html,body{width:1200px;height:4455px;overflow:hidden}
body{position:relative;background:var(--white);font-family:"Open Sans",Arial,sans-serif;color:var(--body)}
.abs{position:absolute}
.shape{position:absolute;left:0;width:1200px}
.heading{position:absolute;left:0;width:1200px;text-align:center;font-family:"Poppins",Arial,sans-serif;font-weight:700;color:var(--ink);font-size:31px}
.rule{position:absolute;left:585px;width:30px;height:4px;background:var(--blue)}
.logo-name{font-family:"Poppins",Arial,sans-serif;font-weight:500;color:var(--white);letter-spacing:6px;text-transform:uppercase;line-height:1.05}
.logo-square{position:absolute;background:var(--white)}

/* header */
.hero-photo{position:absolute;left:0;top:0;width:1200px;height:770px;background:linear-gradient(120deg,#5b5546 0%,#8d7f63 45%,#c7b99a 70%,#7b8a5c 100%)}
.site-logo{left:150px;top:24px}
.site-logo .logo-square{left:0;top:8px;width:60px;height:60px}
.site-logo .logo-name{position:absolute;left:78px;top:0;font-size:22px;white-space:nowrap}
.cta{left:737px;top:18px;width:318px;height:42px;border:2px solid var(--white);color:var(--white);font:600 13px "Poppins",Arial,sans-serif;display:flex;align-items:center;justify-content:center;letter-spacing:.3px}
.nav{left:565px;top:86px;display:flex;gap:0;font:600 12.5px "Poppins",Arial,sans-serif;color:var(--white)}
.nav span{position:absolute;white-space:nowrap}
.screen{left:0;top:150px;width:640px;height:445px;background:var(--white);border:10px solid #2d2d30;border-left:none}
.screen .logo-sq{position:absolute;left:135px;top:90px;width:66px;height:66px;background:var(--blue)}
.screen .logo-name{position:absolute;left:220px;top:84px;font-size:25px;color:var(--navy)}
.screen p{position:absolute;left:90px;top:215px;width:460px;text-align:center;font-size:16.5px;line-height:24px;color:var(--ink)}
.dots{display:flex;gap:9px;align-items:center}
.dots i{display:block;width:9px;height:9px;border-radius:50%;background:var(--white);opacity:.85}
.dots i.on{width:14px;height:14px;background:none;border:2px solid var(--white)}

/* tiles */
.tile{position:absolute;width:290px;height:247px;overflow:hidden}
.tile .fill{position:absolute;inset:0}
.tile .label{position:absolute;left:30px;bottom:18px;width:240px;font:700 14.5px/17px "Poppins",Arial,sans-serif;color:var(--white);text-transform:uppercase}
.tile .label::before{content:"";display:block;width:22px;height:3px;background:var(--blue);margin-bottom:7px}

/* about */
.portrait{left:150px;top:1530px;width:296px;height:296px;border-radius:50%;border:10px solid var(--white);box-shadow:0 0 0 2px #ddd;background:radial-gradient(circle at 50% 40%,#9a7f6c,#4a3d36 70%,#6f7a7c)}
.about-title{left:594px;top:1500px;font:700 40px "Poppins",Arial,sans-serif;color:var(--ink)}
.about-sub{left:594px;top:1555px;font:600 24px "Poppins",Arial,sans-serif;color:var(--ink)}
.about-text{left:594px;top:1636px;width:470px;font-size:14.5px;line-height:21px;color:var(--body)}
.btn{position:absolute;background:var(--blue);color:var(--white);font:700 13px "Poppins",Arial,sans-serif;display:flex;align-items:center;justify-content:center;text-transform:uppercase}

/* testimonials */
.quote-mark{font:700 64px/1 Georgia,serif;color:var(--white)}
.quote{width:375px;font-size:15px;line-height:21.5px;color:var(--white)}
.by-rule{width:30px;height:2px;background:var(--white)}
.by-name{font:700 15px "Poppins",Arial,sans-serif;color:var(--white)}
.by-role{font-size:11.5px;color:var(--white)}

/* media */
.media-tile .label::before{display:none}
.media-tile .label{font-size:18px;bottom:60px}
.media-tile .btn{left:30px;bottom:22px;width:56px;height:26px;font-size:11px}

/* work history */
.partner{font:600 17px "Poppins",Arial,sans-serif;color:#5a5a62;text-align:center;display:flex;align-items:center;gap:8px}
.partner b{display:block;width:14px;height:14px;background:#c6c6cc;flex:none}

/* form */
.field{position:absolute;border:1px solid var(--line);background:var(--white);font-size:11px;color:#666;padding:0 12px;display:flex;align-items:center;text-transform:uppercase}
.field.area{align-items:flex-start;padding-top:14px}

/* footer */
.foot-logo .logo-square{left:0;top:10px;width:78px;height:78px}
.foot-logo .logo-name{position:absolute;left:108px;top:0;font-size:29px;white-space:nowrap}
.foot-menu{font:700 12px "Poppins",Arial,sans-serif;color:var(--white)}
.foot-links{font:500 11.5px "Poppins",Arial,sans-serif;color:var(--white);white-space:nowrap}
.foot-copy{font-size:11px;color:#cfd0d6}
</style>
</head>
<body>

<!-- HERO -->
<div class="hero-photo" role="img" aria-label="Photo of the founder presenting in a classroom beside a display screen"></div>
<div class="abs screen">
  <div class="logo-sq"></div>
  <div class="logo-name">Brightwater<br>Civic<br>Advisors</div>
  <p>Brightwater Civic Advisors supports nonprofit organizations and educational institutions to carry out their missions to benefit the wider community</p>
</div>
<div class="abs site-logo">
  <div class="logo-square"></div>
  <div class="logo-name">Brightwater<br>Civic<br>Advisors</div>
</div>
<div class="abs cta">BOOK A COMPLIMENTARY CONSULTATION</div>
<div class="abs nav">
  <span style="left:0;top:0">ABOUT</span>
  <span style="left:80px;top:0">SERVICES &amp; TESTIMONIALS</span>
  <span style="left:275px;top:0">MEDIA &amp; IMPACT</span>
  <span style="left:421px;top:0">CONTACT</span>
</div>
<div class="abs dots" style="left:550px;top:624px"><i></i><i></i><i class="on"></i><i></i><i></i></div>
<svg class="shape" style="top:650px" width="1200" height="125" viewBox="0 0 1200 125">
  <polygon points="720,95 1200,50 1200,62 760,100" fill="#7fbf3a"/>
  <polygon points="0,110 600,15 1200,110 1200,125 0,125" fill="#ffffff"/>
</svg>

<!-- SERVICES -->
<h2 class="heading" style="top:740px">Services</h2>
<div class="rule" style="top:795px"></div>
<div class="tile" style="left:143px;top:840px"><div class="fill" role="img" aria-label="Photo of staff at a professional development workshop" style="background:linear-gradient(160deg,#3a2a33,#6b4a5a 60%,#2c2a3a)"></div><div class="label">Staff Professional Development</div></div>
<div class="tile" style="left:455px;top:840px"><div class="fill" role="img" aria-label="Photo of a community partnership group" style="background:linear-gradient(160deg,#4a3b36,#7a6356 60%,#2f2a2c)"></div><div class="label">Community Partnership Development</div></div>
<div class="tile" style="left:763px;top:840px"><div class="fill" role="img" aria-label="Photo of a facilitated group session" style="background:linear-gradient(160deg,#8a6e4c,#5e4a3a 60%,#3a312c)"></div><div class="label">Group Facilitation &amp; Leadership Training</div></div>
<div class="tile" style="left:143px;top:1108px"><div class="fill" role="img" aria-label="Photo of an audience at a program presentation" style="background:linear-gradient(160deg,#5a3a36,#3a3034 60%,#25232a)"></div><div class="label">Program Design, Implementation, &amp; Evaluation</div></div>
<div class="tile" style="left:455px;top:1108px"><div class="fill" role="img" aria-label="Photo of an event in a wood panelled hall" style="background:linear-gradient(160deg,#6a4a32,#4a3528 60%,#2e2520)"></div><div class="label">Event Planning</div></div>
<div class="tile" style="left:763px;top:1108px"><div class="fill" role="img" aria-label="Photo of a leadership team standing together" style="background:linear-gradient(160deg,#6c6a72,#44424a 60%,#2a2a30)"></div><div class="label">Strategic Planning &amp; Visioning</div></div>

<!-- ABOUT -->
<div class="shape" style="top:1417px;height:560px;background:var(--mist)"></div>
<div class="abs portrait" role="img" aria-label="Portrait photo of founder Mara Ellison"></div>
<div class="abs about-title">About</div>
<div class="abs about-sub">Brightwater Civic Advisors</div>
<div class="rule" style="left:594px;top:1603px"></div>
<p class="abs about-text">Founder Mara Ellison is an educator with a 22-year record of demonstrated achievement and leadership roles in nonprofits and educational institutions. Most recently, she served as Associate Dean of Students in the University and Director of the Campus Civic Service Office at Lakeshore State University.</p>
<div class="btn" style="left:603px;top:1785px;width:122px;height:35px">Read More</div>

<!-- TESTIMONIALS -->
<svg class="shape" style="top:1900px" width="1200" height="665" viewBox="0 0 1200 665">
  <polygon points="0,75 600,0 1200,75 1200,560 600,665 0,560" fill="#3b87d3"/>
</svg>
<h2 class="heading" style="top:1983px;color:var(--white)">Testimonials</h2>
<div class="rule" style="top:2037px;background:var(--white)"></div>
<div class="abs quote-mark" style="left:150px;top:2110px">&ldquo;</div>
<p class="abs quote" style="left:193px;top:2148px">Daniel has an uncanny ability to combine social change theory and real-world practice in truly compelling ways. For five years at Lakeshore State University, I saw first-hand how Mara inspired legions of students, created innovative programs, and transformed relationships with community stakeholders. Best of all, she did it with integrity, smarts, enthusiasm and a warm, infectious spirit.</p>
<div class="abs by-rule" style="left:193px;top:2322px"></div>
<div class="abs by-name" style="left:193px;top:2336px">Daniel Ortell,</div>
<div class="abs by-role" style="left:193px;top:2358px">VP, Chief Content Officer, KVRN Public Radio</div>
<div class="abs" style="left:600px;top:2125px;width:1px;height:230px;background:rgba(255,255,255,.5)"></div>
<div class="abs quote-mark" style="left:683px;top:2110px">&ldquo;</div>
<p class="abs quote" style="left:716px;top:2148px">Mara has a unique ability to bring people and institutions together. Mara's ability to lead and expertly facilitate thoughtful and productive conversations has yielded tangible results that are demonstrated in the strong and lasting community partnerships she has helped create.</p>
<div class="abs by-rule" style="left:716px;top:2322px"></div>
<div class="abs by-name" style="left:716px;top:2336px">Nadia Brooks</div>
<div class="abs by-role" style="left:716px;top:2358px">Executive Director, Open Door Community Partners</div>
<div class="abs dots" style="left:560px;top:2402px"><i></i><i></i><i class="on"></i><i></i><i></i></div>

<!-- MEDIA & IMPACT -->
<h2 class="heading" style="top:2550px">Media &amp; Impact</h2>
<div class="rule" style="top:2605px"></div>
<div class="tile media-tile" style="left:143px;top:2667px;height:318px"><div class="fill" role="img" aria-label="Photo of a speaker at a conference podium" style="background:linear-gradient(160deg,#1c2a4a,#3a4a6a 55%,#2a2420)"></div><div class="label">Articles</div><div class="btn">Read</div></div>
<div class="tile media-tile" style="left:455px;top:2667px;height:318px"><div class="fill" role="img" aria-label="Photo of a presenter speaking to a large audience" style="background:linear-gradient(160deg,#c9c4bc,#8a8278 55%,#3a3632)"></div><div class="label">Videos</div><div class="btn">View</div></div>
<div class="tile media-tile" style="left:763px;top:2667px;height:318px"><div class="fill" role="img" aria-label="Photo of a podcast conversation around a table" style="background:linear-gradient(160deg,#7a4a2a,#4a3024 55%,#2a201c)"></div><div class="label">Podcasts</div><div class="btn">Listen</div></div>

<!-- WORK HISTORY -->
<svg class="shape" style="top:3085px" width="1200" height="430" viewBox="0 0 1200 430">
  <polygon points="0,80 600,0 1200,80 1200,355 600,425 0,355" fill="#f3f1f1"/>
</svg>
<h2 class="heading" style="top:3168px">Work History</h2>
<div class="rule" style="top:3222px"></div>
<svg class="abs" style="left:76px;top:3316px" width="16" height="28" viewBox="0 0 16 28"><polyline points="14,2 2,14 14,26" fill="none" stroke="#9a9aa2" stroke-width="2.5"/></svg>
<svg class="abs" style="left:1118px;top:3316px" width="16" height="28" viewBox="0 0 16 28"><polyline points="2,2 14,14 2,26" fill="none" stroke="#9a9aa2" stroke-width="2.5"/></svg>
<div class="abs partner" style="left:140px;top:3318px;width:160px;font-size:13px">Campus Civic Service Office</div>
<div class="abs partner" style="left:308px;top:3318px;width:120px;justify-content:center"><b></b>Forum Fellows</div>
<div class="abs partner" style="left:435px;top:3318px;width:240px;justify-content:center">Harbor Bay Charter Schools</div>
<div class="abs partner" style="left:690px;top:3318px;width:210px;justify-content:center">Civic Learning Lab</div>
<div class="abs partner" style="left:920px;top:3318px;width:170px;justify-content:center"><b style="border-radius:50%"></b>ServeNation</div>

<!-- CONTACT -->
<h2 class="heading" style="top:3515px">Contact</h2>
<div class="rule" style="top:3570px"></div>
<div class="field" style="left:273px;top:3630px;width:321px;height:41px">First Name</div>
<div class="field" style="left:612px;top:3630px;width:321px;height:41px">Last Name</div>
<div class="field" style="left:273px;top:3692px;width:321px;height:41px">Organization Name</div>
<div class="field" style="left:612px;top:3692px;width:321px;height:41px">Email Address</div>
<div class="field" style="left:273px;top:3757px;width:660px;height:41px">Subject</div>
<div class="field area" style="left:273px;top:3816px;width:660px;height:146px">Message</div>
<div class="btn" style="left:538px;top:3997px;width:122px;height:39px">Submit</div>

<!-- FOOTER -->
<svg class="shape" style="top:4125px" width="1200" height="330" viewBox="0 0 1200 330">
  <polygon points="0,110 600,0 1200,110 1200,330 0,330" fill="#2a2c38"/>
</svg>
<div class="abs foot-logo" style="left:148px;top:4262px">
  <div class="logo-square"></div>
  <div class="logo-name">Brightwater<br>Civic<br>Advisors</div>
</div>
<div class="abs" style="left:630px;top:4265px;width:1px;height:110px;background:rgba(255,255,255,.35)"></div>
<div class="abs foot-menu" style="left:671px;top:4272px">MENU</div>
<div class="abs foot-links" style="left:671px;top:4308px">ABOUT &nbsp;|&nbsp; SERVICES &amp; TESTIMONIALS &nbsp;|&nbsp; MEDIA &amp; IMPACT &nbsp;|&nbsp; CONTACT</div>
<div class="abs foot-copy" style="left:671px;top:4368px">Copyright &copy; 2019 All Rights Reserved</div>

</body>
</html>
```